Business Card Design Project

Business Card
We are rebranding with a new logo
Industry/Entity Type
Business
Contact Information for Business Card
Dennis Morvale +61 487215963 dennis@quorv.com.au P.O. Box 872 Fernlow QLD 4309
Requirements
Must have
- Logo

```html
<!DOCTYPE html>
<html lang="en">
<head>
<meta charset="utf-8">
<title>Quorv International – Business Card</title>
<link rel="stylesheet" href="https://fonts.googleapis.com/css2?family=Roboto:wght@400;500;700&family=Roboto+Condensed:wght@700&display=swap">
<style>
  :root {
    --backdrop: #2a2a2a;
    --card-white: #f3f3f3;
    --brand-blue: #1a86b8;
    --deep-blue: #0d5e86;
    --bright-blue: #1a9ad2;
    --orange: #f08a1c;
    --burnt-orange: #d8581f;
    --text-white: #ffffff;
  }
  * { margin: 0; padding: 0; box-sizing: border-box; }
  html, body {
    width: 1200px;
    height: 960px;
    overflow: hidden;
    background: var(--backdrop);
  }
  .card {
    position: absolute;
    left: 223px;
    top: 265px;
    width: 754px;
    height: 430px;
    border-radius: 18px;
    overflow: hidden;
    background: var(--card-white);
    font-family: "Roboto", Arial, sans-serif;
  }
  .card-swoosh {
    position: absolute;
    inset: 0;
    width: 100%;
    height: 100%;
  }
  .brand {
    position: absolute;
    left: 62px;
    top: 70px;
    color: var(--brand-blue);
    font-family: "Roboto", Arial, sans-serif;
    font-weight: 500;
    line-height: 1;
  }
  .brand-name {
    display: block;
    font-size: 84px;
    letter-spacing: -1px;
  }
  .brand-tagline {
    display: block;
    margin-top: 10px;
    font-size: 21px;
    letter-spacing: 4.6px;
  }
  .contact {
    position: absolute;
    right: 32px;
    top: 256px;
    text-align: right;
    color: var(--text-white);
  }
  .contact-name {
    font-family: "Roboto Condensed", Arial, sans-serif;
    font-weight: 700;
    font-size: 26px;
    color: var(--orange);
    margin-bottom: 12px;
    margin-right: 0;
  }
  .contact-line {
    display: flex;
    justify-content: flex-end;
    align-items: center;
    gap: 8px;
    font-size: 17px;
    height: 24px;
  }
  .contact-line.address { margin-top: 5px; }
  .contact-icon {
    width: 15px;
    height: 15px;
    fill: var(--orange);
    flex: none;
  }
</style>
</head>
<body>
  <div class="card">
    <svg class="card-swoosh" viewBox="0 0 754 430" preserveAspectRatio="none" aria-hidden="true">
      <defs>
        <radialGradient id="blueField" cx="0.55" cy="0.75" r="0.7">
          <stop offset="0" stop-color="var(--bright-blue)"/>
          <stop offset="1" stop-color="var(--deep-blue)"/>
        </radialGradient>
      </defs>
      <path d="M660 0 L754 0 L754 20 C640 190 450 300 230 375 C420 280 610 170 660 0 Z" fill="var(--burnt-orange)"/>
      <path d="M598 0 L662 0 C640 150 470 300 230 378 C420 290 590 170 598 0 Z" fill="var(--orange)"/>
      <path d="M754 8 L754 430 L0 430 L0 428 C300 400 600 250 754 8 Z" fill="url(#blueField)"/>
      <path d="M20 428 C300 400 600 250 748 8" fill="none" stroke="#ffffff" stroke-width="1.5"/>
    </svg>

    <div class="brand">
      <span class="brand-name">Quorv</span>
      <span class="brand-tagline">INTERNATIONAL</span>
    </div>

    <div class="contact">
      <div class="contact-name">DENNIS MORVALE</div>
      <div class="contact-line">+61 487215963
        <svg class="contact-icon" viewBox="0 0 16 16"><path d="M3.5 1 L6 1 L7 4.5 L5.3 5.8 C6.2 7.8 8.2 9.8 10.2 10.7 L11.5 9 L15 10 L15 12.5 C15 13.9 13.9 15 12.5 15 C6.2 15 1 9.8 1 3.5 C1 2.1 2.1 1 3.5 1 Z"/></svg>
      </div>
      <div class="contact-line">dennis@quorv.com.au
        <svg class="contact-icon" viewBox="0 0 16 16"><path d="M1 3 H15 V13 H1 Z M2 4.2 V4.8 L8 9 L14 4.8 V4.2 Z" fill-rule="evenodd"/></svg>
      </div>
      <div class="contact-line">www.quorv.com.au
        <svg class="contact-icon" viewBox="0 0 16 16"><circle cx="8" cy="8" r="7"/><path d="M4 5 C6 5 7 7 6 9 C5 10 6 12 7 13 M11 3 C10 5 12 6 13 7 M9 10 C10 9 12 10 12 12" stroke="#0d5e86" stroke-width="1.2" fill="none"/></svg>
      </div>
      <div class="contact-line address">P.O. Box 872 Fernlow QLD 4309
        <svg class="contact-icon" viewBox="0 0 16 16"><path d="M8 1 C5 1 3 3.2 3 6 C3 9.5 8 15 8 15 C8 15 13 9.5 13 6 C13 3.2 11 1 8 1 Z M8 4 A2 2 0 1 0 8 8 A2 2 0 1 0 8 4 Z" fill-rule="evenodd"/></svg>
      </div>
    </div>
  </div>
</body>
</html>
```